Einladungskarten-Design für jährliches Sommerfest
Zielgruppe
Wir sind die Kreisverwaltung des Landkreises Darmstadt-Dieburg (das Landratsamt) und möchten unsere Mitarbeiter zum jährlichen Sommerfest einladen. Jedes Jahr stehen diese Feste unter einem anderen Motto- das diesjährige lautet: Karibik.
Aufgabenstellung
Wegen des karibischen Mottos möchten wir die Einladung in Form einer Postkarte designen lassen (vorne Bild, hinten Text). Das Design soll uns als druckfähige Datei in einem gängigen Postkarten-Format zugehen, das sich über Bogen-Blitz oder Falz-und-Papier produzieren lässt. Bitte integrieren Sie wenn möglich keine kostenpflichtigen Bilder oder Schriftarten. Der Text lautet:
Liebe Kolleginnen und Kollegen,
Gundula Brettschneider, Hannelore Wiest und ich senden Euch Urlaubsgrüße aus der Karibik!
Hier ist es so schön, dass wir Euch direkt einladen möchten – zu einer „Karibischen Nacht“ am Donnerstag, 16. August ab 17 Uhr.
Wir feiern natürlich am Strand (Amtshof Lindenau, direkt am See). Dresscode: sommerlich, blumig, legere!
Bei einem kühlen Getränk oder fruchtigem Cocktail an der Bar wollen wir mit euch ins Gespräch kommen und einen gemütlichen Sommerabend verbringen.
Dieser Kurzurlaub ist bereits vom Fachbereich Personal genehmigt und kostet Euch lediglich fünf Euro pro Person. In unserer vier Sterne Club-Anlage sind Abendessen vom Buffet, alkoholfreie Getränke und zwei Stunden Zeitgutschrift inklusive.
Eure Reiseunterlagen könnt Ihr über das Personal-Info-System bis Mittwoch, 8. August reservieren.
Sommerliche Grüße
Landrat Jürgen Otto Baumbusch

```html
<!DOCTYPE html>
<html lang="de">
<head>
<meta charset="utf-8">
<title>Karibische Nacht – Einladungspostkarte</title>
<link rel="stylesheet" href="https://fonts.googleapis.com/css2?family=Yellowtail&family=Raleway:wght@300;400&display=swap">
<style>
  :root {
    --page: #ffffff;
    --cream: #f3f2ec;
    --leaf-dark: #1f8a3c;
    --leaf: #36a852;
    --leaf-light: #7cc46a;
    --hibiscus: #e6407a;
    --hibiscus-soft: #f07aa3;
    --sun: #f7b733;
    --ink: #3c3c3c;
    --accent: #e01e64;
    --brown: #6b4226;
    --stamp: #f4d8c8;
  }
  * { margin: 0; padding: 0; box-sizing: border-box; }
  html, body { width: 800px; height: 1200px; overflow: hidden; background: var(--page); }
  .canvas { position: relative; width: 800px; height: 1200px; background: var(--page); }
  .script { font-family: "Yellowtail", cursive; font-weight: 400; color: var(--accent); }

  .postcard {
    position: absolute; left: 97px; width: 607px; height: 429px;
    box-shadow: 0 2px 4px rgba(0,0,0,.18);
    overflow: hidden;
  }
  .postcard--front { top: 133px; }
  .postcard--back { top: 638px; }

  .jungle-art {
    position: absolute; inset: 0;
    background:
      radial-gradient(ellipse 60% 45% at 22% 15%, var(--hibiscus-soft) 0 30%, transparent 60%),
      radial-gradient(ellipse 40% 35% at 48% 8%, var(--sun) 0 30%, transparent 60%),
      radial-gradient(ellipse 45% 40% at 88% 20%, var(--hibiscus-soft) 0 30%, transparent 60%),
      radial-gradient(ellipse 40% 35% at 83% 82%, var(--sun) 0 30%, transparent 60%),
      radial-gradient(ellipse 40% 35% at 45% 90%, var(--hibiscus) 0 30%, transparent 60%),
      radial-gradient(ellipse 62% 48% at 50% 50%, var(--cream) 0 55%, transparent 85%),
      linear-gradient(135deg, var(--leaf) 0%, var(--leaf-dark) 50%, var(--leaf-light) 100%);
  }
  .postcard--back .jungle-art {
    background:
      radial-gradient(ellipse 30% 28% at 10% 12%, var(--hibiscus) 0 40%, transparent 70%),
      radial-gradient(ellipse 25% 20% at 50% 5%, var(--sun) 0 40%, transparent 70%),
      radial-gradient(ellipse 25% 30% at 95% 20%, var(--hibiscus-soft) 0 40%, transparent 70%),
      radial-gradient(ellipse 25% 25% at 92% 88%, var(--sun) 0 40%, transparent 70%),
      linear-gradient(135deg, var(--leaf) 0%, var(--leaf-dark) 50%, var(--leaf-light) 100%);
  }

  .front-title {
    position: absolute; left: 124px; top: 148px;
    font-size: 66px; line-height: 62px; transform: rotate(-4deg);
    white-space: nowrap;
  }
  .front-title span { display: block; }
  .front-title span + span { padding-left: 34px; }

  .letter-panel {
    position: absolute; left: 49px; top: 38px; width: 509px; height: 361px;
    background: var(--cream);
  }
  .letter {
    position: absolute; left: 23px; top: 0; width: 470px; height: 361px;
    font-family: "Raleway", sans-serif; font-weight: 300; color: var(--ink);
  }
  .letter-salutation {
    position: absolute; left: 0; top: 40px; width: 372px;
    text-align: center; white-space: nowrap;
    font-size: 22px; line-height: 26px;
  }
  .letter-intro {
    position: absolute; left: 0; top: 78px; width: 372px;
    text-align: center; white-space: nowrap; font-size: 11.2px; line-height: 14px;
  }
  .letter-event {
    position: absolute; left: 0; top: 132px; white-space: nowrap;
    font-size: 17px; line-height: 22px;
  }
  .letter-body {
    position: absolute; left: 0; top: 160px; white-space: nowrap;
    font-size: 10.2px; line-height: 14.1px;
  }
  .letter-closing {
    position: absolute; left: 0; top: 329px;
    font-size: 10.2px; line-height: 14px;
  }
  .letter-signature {
    position: absolute; left: 221px; top: 326px; white-space: nowrap;
    font-size: 17px; line-height: 20px;
  }

  .address-lines { position: absolute; left: 306px; top: 194px; width: 182px; }
  .address-lines span { display: block; height: 25.5px; border-bottom: 1px solid var(--brown); }

  .postage { position: absolute; left: 395px; top: 40px; width: 95px; height: 100px; }
</style>
</head>
<body>
<main class="canvas">

  <section class="postcard postcard--front" aria-label="Vorderseite">
    <div class="jungle-art" role="img" aria-label="Aquarell-Illustration: Palmblätter, Monstera, pinke und gelbe Hibiskusblüten und Wassereis am Stiel rund um die Kartenränder"></div>
    <h1 class="front-title script"><span>Post aus</span><span>der Karibik</span></h1>
  </section>

  <section class="postcard postcard--back" aria-label="Rückseite">
    <div class="jungle-art" role="img" aria-label="Aquarell-Rahmen aus Palmblättern, Hibiskusblüten und Wassereis"></div>
    <div class="letter-panel">
      <svg class="postage" viewBox="0 0 95 100" aria-hidden="true">
        <rect x="32" y="8" width="60" height="72" fill="var(--stamp)"/>
        <circle cx="26" cy="26" r="25" fill="var(--cream)" stroke="var(--brown)" stroke-width="1.5"/>
        <circle cx="26" cy="26" r="20" fill="none" stroke="var(--brown)" stroke-width="1"/>
        <g fill="none" stroke="var(--brown)" stroke-width="1">
          <path d="M9 70 q6-4 12 0 t12 0 t12 0 t12 0 t12 0"/>
          <path d="M9 76 q6-4 12 0 t12 0 t12 0 t12 0 t12 0"/>
          <path d="M9 82 q6-4 12 0 t12 0 t12 0 t12 0 t12 0"/>
          <path d="M9 88 q6-4 12 0 t12 0 t12 0 t12 0 t12 0"/>
        </g>
      </svg>
      <div class="address-lines" aria-label="Adressfeld"><span></span><span></span><span></span></div>
      <div class="letter">
        <h2 class="letter-salutation script">Liebe Kolleginnen und Kollegen,</h2>
        <p class="letter-intro">Gundula Brettschneider, Hannelore Wiest und ich senden Euch<br>Urlaubsgrüße aus der Karibik!<br>Hier ist es so schön, dass wir Euch direkt einladen möchten – zu einer</p>
        <p class="letter-event script">„Karibischen Nacht“ am Donnerstag, 16. August ab 17 Uhr.</p>
        <p class="letter-body">Wir feiern natürlich am Strand (Amtshof Lindenau, direkt am See).<br>Dresscode: sommerlich, blumig, legere! Bei einem kühlen<br>Getränk oder fruchtigem Cocktail an der Bar wollen wir mit<br>euch ins Gespräch kommen und einen gemütlichen<br>Sommerabend verbringen. Dieser Kurzurlaub ist bereits<br>vom Fachbereich Personal genehmigt und kostet Euch<br>lediglich fünf Euro pro Person. In unserer vier Sterne<br>Club-Anlage sind Abendessen vom Buffet, alkoholfreie<br>Getränke und zwei Stunden Zeitgutschrift inklusive.<br>Eure Reiseunterlagen könnt Ihr über das Personal-Info-<br>System bis Mittwoch, 8. August reservieren.</p>
        <p class="letter-closing">Sommerliche Grüße</p>
        <p class="letter-signature script">Landrat Jürgen Otto Baumbusch</p>
      </div>
    </div>
  </section>

</main>
</body>
</html>
```